Creative Web Design for an ERP (technology) Consulting Business

I need two pages designed for the ERP Project Management Consulting Company I am starting. One page is the home page, the other page is an important inside page.

I've looked at many different templates for sites like this, and they all look the same to me. I am working with PixelGuild designers because I want something unique.

This site will be implemented with Wordpress using the Elementor framework,

About Me ---
I have worked with PixelGuild several times before, and I have tired to do everything I can to ve helpful. In the uploads, you will find PDF's with wireframes outlning the layout of the pages, as well as explanatios for each section. There are Word documents that you can copy into text. The list below explains the files included.

Although the wireframes suggest a layout, please feel free to use your creativity - often, I find that the designs I like the most are designs I have never thought of.

About the Company --
ERP (Enterprise Resource Planning) systems are business computer systems that tie different businesss functions together. These systems are expensive and complicated, and efforts to implement them often fail. The purpose of the company is to increase the chance of success by focusing on the things that need to be right.

I have uploaded several files to help clarify what I am looking for:
• 1a - Home Page Wireframe - PDF
Wireframe for the home page with an explanation of each section.
• 1b - Home Page Text – Word
A Word document so that you can copy the text.
• 2 - Copper Harbor Logo – ZIP
Four different versions of the company logo in Adobe Illustrator, PNG, and JPG formats. Any of the four are acceptable:
1. Logo_1 – Black on Transparent – Same Line ERP
2. Logo_2 – White on Transparent – Same Line ERP
3. Logo_3 – Black on Transparent – Big ERP on Different Line
4. Logo_4 – White on Transparent – Big ERP on Different Line
• 3a - Copper Harbor Page Wireframe – PDF
Wireframe for he Copper Harbor page, with explanations and a detailed breakdown of the top section.
• 3b - Copper Harbor Text – Word
• 4 - Colors and Palettes – PDF
• 5 - Change Management Icon – EPS
• 6 – Site Map
If you wish to see it, the site map provides an idea of the entire site. The two pages circled in red are the ones I need to be designed.

Thank you for your interest in this project!

Target Market(s)

Corporate decision makers, primarily CIOs and CFOs, as well as ERP project managers and influencers.

Industry/Entity Type

Consulting

Number of Pages Required

2 page

Font styles to use
Sans Serif

Requirements
Must have
• Pages that contain the elements explained on the wireframes provided.
Nice to have
• A design that looks and feels unique
Should not have
• A typical, template layour

```html
<!DOCTYPE html>
<html lang="en">
<head>
<meta charset="utf-8">
<title>Copper Harbor ERP — Home</title>
<link href="https://fonts.googleapis.com/css2?family=Urbanist:wght@400;500;600;700;800&display=swap" rel="stylesheet">
<style>
:root{
  --blue:#0a6fc4;
  --red:#e3262c;
  --orange:#f7941d;
  --green:#19a54a;
  --purple:#6b2d91;
  --ink:#1c1c1c;
  --text:#3b3b3b;
  --muted:#6a6a6a;
  --footer:#1b1b1b;
  --white:#ffffff;
}
*{margin:0;padding:0;box-sizing:border-box}
html,body{width:1200px;height:4351px;overflow:hidden}
body{position:relative;background:var(--white);font-family:"Urbanist",sans-serif;color:var(--text)}
.abs{position:absolute}
.btn{position:absolute;display:flex;align-items:center;justify-content:center;background:var(--blue);color:var(--white);font-weight:700;font-size:15px;border-radius:30px;letter-spacing:.3px}
.play{position:absolute;border-radius:50%;background:var(--red);border:4px solid var(--white);display:flex;align-items:center;justify-content:center;box-shadow:0 6px 16px rgba(0,0,0,.18)}
.photo-circle{position:absolute;border-radius:50%}
.section-title{position:absolute;left:0;width:1200px;text-align:center;font-weight:800;color:var(--ink);font-size:42px;letter-spacing:-.5px}

/* hero */
.hero-photo{left:0;top:0;width:1200px;height:890px;background:linear-gradient(100deg,#2a2320 0%,#4a3a2f 30%,#8a6a4d 55%,#5a5f6a 80%,#30343c 100%)}
.hero-shade{left:0;top:0;width:1200px;height:890px;background:linear-gradient(90deg,rgba(0,0,0,.55) 0%,rgba(0,0,0,.2) 45%,rgba(0,0,0,0) 70%)}
.nav a{position:absolute;top:50px;transform:translateX(-50%);color:var(--white);font-weight:700;font-size:15px;text-decoration:none;white-space:nowrap}
.nav a.active{color:#3a9bff}
.nav-dot{left:194px;top:40px;width:5px;height:5px;border-radius:50%;background:#3a9bff;transform:translateX(-50%)}
.nav-brand{left:600px;top:40px;transform:translateX(-50%);color:var(--white);font-weight:700;font-size:15px;text-align:center;line-height:1.1}
.hero-brand{left:90px;top:220px;width:400px;height:90px;color:var(--white)}
.hero-brand .mark{position:absolute;left:0;top:0;width:84px;height:84px;border-radius:50%;border:12px solid var(--white)}
.hero-brand .name{position:absolute;left:100px;top:22px;font-weight:800;font-size:36px;line-height:1;letter-spacing:.5px;white-space:nowrap}
.hero-copy{left:90px;top:376px;width:360px;color:var(--white);font-size:15px;line-height:1.35}
.hero-list{left:90px;top:450px;color:var(--white);font-size:16px;line-height:1.3;list-style:none}
.mouse-badge{left:563px;top:631px;width:74px;height:74px;border-radius:50%;background:var(--white);box-shadow:0 4px 14px rgba(0,0,0,.15);display:flex;align-items:center;justify-content:center}

/* about */
.about-text{left:290px;top:818px;width:620px;text-align:center;font-size:15.5px;line-height:1.45;color:var(--text)}
.info h3{font-size:17px;font-weight:700;color:var(--ink);margin-bottom:8px}
.info p{font-size:13.5px;line-height:1.38;color:var(--text);margin-bottom:26px}

/* services grid */
.svc{position:absolute;width:360px}
.svc h4{font-size:15.5px;font-weight:800;color:var(--ink)}
.svc p{font-size:12.5px;line-height:1.4;color:var(--text)}
.svc .more{font-size:12.5px;font-weight:800;color:var(--muted);text-decoration:underline}
.svc-left{text-align:right}
.svc-icon{position:absolute;width:80px;height:80px;border-radius:50%;display:flex;align-items:center;justify-content:center}
.center-brand{left:600px;top:1620px;transform:translateX(-50%);text-align:center;width:240px}
.center-brand .ring{width:210px;height:210px;margin:0 auto 14px;border-radius:50%;border:34px solid var(--ink)}
.center-brand span{display:block;font-weight:800;font-size:26px;color:var(--ink);letter-spacing:1px}

/* features */
.feature h2{font-size:40px;font-weight:800;color:var(--ink);line-height:1.12;letter-spacing:-.5px}
.feature p{font-size:14px;line-height:1.45;color:var(--text);margin-top:10px}

/* cards */
.card{position:absolute;top:3127px;height:388px}
.card-label{position:absolute;left:375px;top:3436px;color:var(--white);font-weight:700;font-size:20px}
.card-arrow{left:777px;top:3424px;width:48px;height:48px;border-radius:50%;background:var(--white);display:flex;align-items:center;justify-content:center}

/* subscribe */
.subscribe{left:206px;top:3718px;width:788px;height:208px;border-radius:104px;background:var(--red);box-shadow:0 10px 30px rgba(0,0,0,.25)}
.subscribe h2{position:absolute;left:0;top:36px;width:788px;text-align:center;color:var(--white);font-size:44px;font-weight:800;letter-spacing:-.5px}
.sub-field{position:absolute;left:95px;top:105px;width:598px;height:48px;background:var(--white);border-radius:24px;overflow:hidden}
.sub-field .ph{position:absolute;left:50px;top:15px;font-size:14px;color:#9a9a9a}
.sub-field .submit{position:absolute;right:0;top:0;width:100px;height:48px;background:var(--blue);color:var(--white);font-weight:800;font-size:15px;display:flex;align-items:center;justify-content:center}

/* footer */
.foot-brand{left:90px;top:4062px;width:340px;height:60px;color:var(--white)}
.foot-brand .mark{position:absolute;left:0;top:0;width:52px;height:52px;border-radius:50%;border:8px solid var(--white)}
.foot-brand .name{position:absolute;left:64px;top:12px;font-weight:800;font-size:27px;line-height:1;white-space:nowrap;letter-spacing:-.3px}
.social{position:absolute;top:4141px;width:30px;height:30px;border-radius:50%;border:1px solid #777}
.foot-col h5{font-size:21px;font-weight:700;color:var(--white);margin-bottom:14px}
.foot-col li{list-style:none;font-size:13px;color:#cfcfcf;line-height:27px}
.contact-line{font-size:13px;color:#dcdcdc;line-height:1.3}
.foot-rule{left:90px;top:4279px;width:1020px;height:1px;background:#3a3a3a}
.copyright{left:0;top:4305px;width:1200px;text-align:center;font-size:13px;color:#cfcfcf}
.to-top{left:1134px;top:4257px;width:40px;height:40px;border-radius:50%;background:var(--blue);display:flex;align-items:center;justify-content:center}
</style>
</head>
<body>

<!-- HERO -->
<div class="abs hero-photo" role="img" aria-label="Photo of a consulting team gathered around a computer screen in an office"></div>
<div class="abs hero-shade"></div>
<svg class="abs" style="left:0;top:620px" width="1200" height="280" viewBox="0 620 1200 280">
  <path d="M0 887 Q600 463 1200 887 L1200 900 L0 900 Z" fill="#fff"/>
</svg>

<nav class="nav">
  <div class="abs nav-dot"></div>
  <a class="active" style="left:194px">Home</a>
  <a style="left:280px">About Us</a>
  <a style="left:390px">Our Services</a>
  <a style="left:495px">Framework</a>
  <a style="left:715px">Tidewater</a>
  <a style="left:823px">Resources</a>
  <a style="left:936px">Case Studies</a>
  <a style="left:1043px">Contact</a>
</nav>
<div class="abs nav-brand">Copper<br>Harbor</div>

<div class="abs hero-brand">
  <div class="mark"></div>
  <div class="name">COPPER HARBOR ERP</div>
</div>
<p class="abs hero-copy">Decades in pursuit of excellence in enterprise applications informed by a researched approach to ERP success.&nbsp; We can help you with ERP:</p>
<ul class="abs hero-list">
  <li>- Project Planning</li>
  <li>- Project Management</li>
  <li>- Project Assessments and Turnaround</li>
  <li>- Change Management</li>
</ul>
<div class="btn" style="left:90px;top:561px;width:136px;height:46px">CONTACT</div>

<div class="abs mouse-badge">
  <svg width="20" height="32" viewBox="0 0 20 32"><rect x="1.5" y="1.5" width="17" height="29" rx="8.5" fill="none" stroke="#222" stroke-width="2"/><line x1="10" y1="7" x2="10" y2="13" stroke="#222" stroke-width="2" stroke-linecap="round"/></svg>
</div>

<!-- ABOUT -->
<h2 class="section-title" style="top:762px">ABOUT</h2>
<p class="abs about-text">Hi! I'm Daniel Moreau, a consultant and ERP leader with extensive experience in ERP project management. My journey is shaped by experience, lifelong learning, and a commitment to excellence.</p>

<svg class="abs" style="left:0;top:1280px" width="1200" height="640" viewBox="0 1280 1200 640">
  <defs><linearGradient id="greyFade" x1="0" y1="0" x2="0" y2="1"><stop offset="0" stop-color="#ececec"/><stop offset=".55" stop-color="#f6f6f6"/><stop offset="1" stop-color="#fff"/></linearGradient></defs>
  <path d="M0 1520 Q600 1060 1200 1520 L1200 1920 L0 1920 Z" fill="url(#greyFade)"/>
</svg>

<div class="photo-circle" style="left:174px;top:926px;width:426px;height:426px;background:linear-gradient(135deg,#c9b79a,#7a6a5a 55%,#3c4c6e)" role="img" aria-label="Photo of three colleagues looking at a laptop together"></div>
<div class="play" style="left:506px;top:1238px;width:96px;height:96px"><svg width="18" height="20" viewBox="0 0 18 20"><path d="M2 1 L17 10 L2 19 Z" fill="#fff"/></svg></div>

<div class="abs info" style="left:649px;top:990px;width:380px">
  <h3>LOOKING FOR INFORMATION?</h3>
  <p>This site shares information related to successful ERP implementations within a framework and method based on <b>“whys.”</b></p>
  <h3>LOOKING FOR HELP?</h3>
  <p>My purpose is to help organizations maximize the transformational value of ERP systems while minimizing organizational pain and damage.&nbsp; My approach is the result of years of research into what it takes to be successful in ERP implementations, supported by real-world experience.</p>
</div>

<!-- SERVICES GRID -->
<h2 class="section-title" style="top:1440px">COPPER HARBOR ERP SERVICES</h2>

<div class="svc-icon" style="left:339px;top:1560px;background:var(--orange)"><svg width="40" height="34" viewBox="0 0 40 34" fill="none" stroke="#fff" stroke-width="2"><rect x="3" y="3" width="34" height="22" rx="2"/><path d="M9 19 L16 12 L22 16 L31 8"/><path d="M14 25 L11 32 M26 25 L29 32"/></svg></div>
<div class="svc svc-left" style="left:0;top:1590px;width:330px"><h4>PROJECT PLANNING</h4></div>
<div class="svc svc-left" style="left:57px;top:1654px">
  <p>“Failing to plan is planning to fail” – Edwin Marsh<br>“Everybody has a plan until they get punched.”</p>
  <div class="more" style="margin-top:8px">MORE</div>
</div>

<div class="svc-icon" style="left:339px;top:1761px;background:var(--purple)"><svg width="40" height="36" viewBox="0 0 40 36" fill="none" stroke="#fff" stroke-width="2"><rect x="4" y="12" width="24" height="20" rx="2"/><circle cx="26" cy="10" r="7"/><path d="M9 26 L14 20 L19 24 L24 18"/><path d="M30 26 L36 32"/></svg></div>
<div class="svc svc-left" style="left:0;top:1791px;width:330px"><h4>PROJECT MANAGEMENT</h4></div>
<div class="svc svc-left" style="left:57px;top:1855px">
  <p>Project “Management” is not just about management, it's about leadership. Both are essential.</p>
  <div class="more" style="margin-top:8px">MORE</div>
</div>

<div class="abs center-brand">
  <div class="ring"></div>
  <span>COPPER HARBOR</span>
</div>

<div class="svc-icon" style="left:742px;top:1560px;background:var(--green)"><svg width="40" height="36" viewBox="0 0 40 36" fill="none" stroke="#fff" stroke-width="2"><rect x="3" y="4" width="26" height="28" rx="2"/><path d="M8 12 H22 M8 18 H18 M8 24 H16"/><circle cx="30" cy="24" r="6"/><path d="M34 28 L38 33"/></svg></div>
<div class="svc" style="left:835px;top:1582px;width:240px"><h4>PROJECT ASSESSMENTS &amp; TURNAROUND</h4></div>
<div class="svc" style="left:744px;top:1654px">
  <p>If your project has gone off track, I can help you get it back on the rails.</p>
  <div class="more" style="margin-top:8px">MORE</div>
</div>

<div class="svc-icon" style="left:742px;top:1761px;background:var(--blue)"><svg width="40" height="40" viewBox="0 0 40 40" fill="none" stroke="#fff" stroke-width="2"><path d="M8 14 A13 13 0 0 1 32 12"/><path d="M32 26 A13 13 0 0 1 8 28"/><path d="M32 6 V12 H26 M8 34 V28 H14"/><circle cx="20" cy="20" r="5"/></svg></div>
<div class="svc" style="left:835px;top:1791px;width:240px"><h4>CHANGE MANAGEMENT</h4></div>
<div class="svc" style="left:744px;top:1855px">
  <p>ERP implementations represent major change across many different dimensions, and change is hard.</p>
  <div class="more" style="margin-top:8px">MORE</div>
</div>

<!-- FRAMEWORK -->
<div class="abs feature" style="left:134px;top:2066px;width:440px">
  <h2>COPPER HARBOR ERP<br>FRAMEWORK</h2>
  <p style="margin-top:28px">The number of things you need to do in an ERP implementation boggles the mind.</p>
  <p style="margin-top:6px">It starts with 'why.' Copper Harbor groups hundreds of critical success factors into recurring themes, distilling them into high-level categories that drive success. Copper Harbor simplifies complexity while retaining essential details.</p>
</div>
<div class="btn" style="left:134px;top:2342px;width:125px;height:42px">MORE</div>
<div class="photo-circle" style="left:633px;top:2002px;width:426px;height:426px;background:linear-gradient(140deg,#8d9a8a,#b89a7c 50%,#5a4a3e)" role="img" aria-label="Photo of a group of students studying together around a table"></div>
<div class="play" style="left:630px;top:2313px;width:96px;height:96px"><svg width="18" height="20" viewBox="0 0 18 20"><path d="M2 1 L17 10 L2 19 Z" fill="#fff"/></svg></div>

<!-- TIDEWATER METHOD -->
<div class="photo-circle" style="left:132px;top:2486px;width:426px;height:426px;background:linear-gradient(130deg,#e6e0d6,#c79a72 50%,#d2571f 85%)" role="img" aria-label="Photo of three colleagues reviewing a tablet together"></div>
<div class="play" style="left:464px;top:2800px;width:96px;height:96px"><svg width="18" height="20" viewBox="0 0 18 20"><path d="M2 1 L17 10 L2 19 Z" fill="#fff"/></svg></div>
<div class="abs feature" style="left:632px;top:2556px;width:430px">
  <h2>TIDEWATER METHOD</h2>
  <p style="margin-top:18px">The framework covers the “why” and “what.” Tidewater is the “how, when,” and “who.”</p>
  <p style="margin-top:18px">Tidewater, drawing from the principles of waterfall planning and agile execution, is designed to be adaptable.&nbsp; It can be overlaid on any methodology, giving you the confidence that all critical elements will be addressed.</p>
</div>
<div class="btn" style="left:635px;top:2778px;width:125px;height:42px">MORE</div>

<!-- SERVICES CARDS -->
<svg class="abs" style="left:0;top:2940px" width="1200" height="260" viewBox="0 2940 1200 260">
  <defs><linearGradient id="warmFade" x1="0" y1="0" x2="0" y2="1"><stop offset="0" stop-color="#fdeee0"/><stop offset="1" stop-color="#fff"/></linearGradient></defs>
  <path d="M0 3140 Q600 2770 1200 3140 L1200 3200 L0 3200 Z" fill="url(#warmFade)"/>
</svg>
<h2 class="section-title" style="top:3030px">COPPER HARBOR ERP SERVICES</h2>

<div class="card" style="left:90px;width:233px;background:linear-gradient(160deg,#d8d2c8,#8a6e58 60%,#4a3a30)" role="img" aria-label="Photo of two colleagues discussing a document"></div>
<div class="card" style="left:338px;width:522px;background:linear-gradient(160deg,#e4e2de,#b9a58c 45%,#6a5a4c 80%,#3a3430)" role="img" aria-label="Photo of a team meeting around a conference table"></div>
<div class="abs" style="left:338px;top:3360px;width:522px;height:155px;background:linear-gradient(180deg,rgba(0,0,0,0),rgba(0,0,0,.45))"></div>
<div class="card-label">Project Management</div>
<div class="abs card-arrow"><svg width="18" height="14" viewBox="0 0 18 14" fill="none" stroke="#222" stroke-width="2"><path d="M1 7 H16 M10 1 L16 7 L10 13"/></svg></div>
<div class="card" style="left:875px;width:235px;background:linear-gradient(160deg,#e8e4de,#b04a30 45%,#7a7a7a 80%)" role="img" aria-label="Photo of colleagues working at a desk with a laptop"></div>

<div class="btn" style="left:537px;top:3567px;width:125px;height:42px">MORE</div>

<!-- FOOTER BACKGROUND -->
<svg class="abs" style="left:0;top:3760px" width="1200" height="591" viewBox="0 3760 1200 591">
  <path d="M0 4005 Q600 3570 1200 4005 L1200 4351 L0 4351 Z" fill="#1b1b1b"/>
</svg>

<!-- SUBSCRIBE -->
<div class="abs subscribe">
  <h2>SUBSCRIBE FOR UPDATE</h2>
  <div class="sub-field">
    <svg class="abs" style="left:22px;top:17px" width="18" height="14" viewBox="0 0 18 14" fill="none" stroke="#9a9a9a" stroke-width="1.6"><rect x="1" y="1" width="16" height="12" rx="1"/><path d="M1 2 L9 8 L17 2"/></svg>
    <span class="ph">Enter your email address</span>
    <div class="submit">SUBMIT</div>
  </div>
</div>

<!-- FOOTER -->
<div class="abs foot-brand">
  <div class="mark"></div>
  <div class="name">COPPER HARBOR ERP</div>
</div>
<div class="social" style="left:181px"></div>
<div class="social" style="left:222px"></div>
<div class="social" style="left:264px"></div>
<div class="social" style="left:303px"></div>

<div class="abs foot-col" style="left:480px;top:4034px">
  <h5>ERP Tools</h5>
  <ul><li>› Copper Harbor</li><li>› Tidewater Method</li><li>› Tools and Resources</li></ul>
</div>
<div class="abs foot-col" style="left:686px;top:4034px">
  <h5>Services</h5>
  <ul><li>› About</li><li>› Project Planning</li><li>› Project Management</li><li>› Project Assessment &amp; Turnaround</li><li>› Change Management</li></ul>
</div>
<div class="abs foot-col" style="left:938px;top:4034px">
  <h5>Contact</h5>
</div>
<svg class="abs" style="left:938px;top:4076px" width="15" height="12" viewBox="0 0 15 12"><rect width="15" height="12" rx="1.5" fill="#2b8be0"/><path d="M1 1.5 L7.5 6.5 L14 1.5" fill="none" stroke="#fff" stroke-width="1.3"/></svg>
<div class="abs contact-line" style="left:960px;top:4074px">Email:<br>dmoreau@copperharborerp</div>
<svg class="abs" style="left:938px;top:4130px" width="15" height="15" viewBox="0 0 24 24"><path d="M6.6 10.8a15.1 15.1 0 0 0 6.6 6.6l2.2-2.2c.3-.3.7-.4 1-.2 1.1.4 2.3.6 3.6.6.6 0 1 .4 1 1V20c0 .6-.4 1-1 1A17 17 0 0 1 3 4c0-.6.4-1 1-1h3.5c.6 0 1 .4 1 1 0 1.3.2 2.5.6 3.6.1.3 0 .7-.2 1z" fill="#2b8be0"/></svg>
<div class="abs contact-line" style="left:960px;top:4128px">Phone:<br>(555) 014-2287</div>

<div class="abs foot-rule"></div>
<div class="abs copyright">© Copyright 2024 Copper Harbor ERP, All Rights Reserved</div>
<div class="abs to-top"><svg width="12" height="8" viewBox="0 0 12 8" fill="none" stroke="#fff" stroke-width="2"><path d="M1 7 L6 2 L11 7"/></svg></div>

</body>
</html>
```